Business cards and stationary design

We just completed the design of our new logo and we need to print new business cards and letterhead for our nonprofit. We are looking for a fresh new design that shows off our new logo. On letterhead, we must have a column on the right or left to include our Board of Directors (up to 45 names) (see attachment)

Industry/Entity Type

Non-Profit

Contact Information for Business Card

Standard business card with name, title, Company name, mailing address phone numbers, email address and website. Tagline on back "Guiding every family home"

Font styles to use
Sans Serif

Requirements
Must have
• include pertinent information above
• new logo
• fonts compatible with logo
• should use logo colors only
Nice to have
• tag lines

```html
<!DOCTYPE html>
<html lang="en">
<head>
<meta charset="utf-8">
<title>Homeward Haven Center — Business Card</title>
<link rel="stylesheet" href="https://fonts.googleapis.com/css2?family=Michroma&family=Libre+Baskerville&display=swap">
<style>
  :root {
    --teal: #0a7fa0;
    --red: #e3232c;
    --ink: #444a4f;
    --paper: #ffffff;
    --backdrop: #d9dcdf;
    --rule: #3a8fb0;
  }
  * { box-sizing: border-box; margin: 0; padding: 0; }
  html, body { width: 1200px; height: 1200px; overflow: hidden; }
  body {
    background: var(--backdrop);
    position: relative;
    font-family: "Libre Baskerville", Georgia, serif;
  }
  .card {
    position: absolute;
    left: 200px;
    width: 800px;
    height: 457px;
    box-shadow: 0 6px 18px rgba(0,0,0,.18);
  }
  /* Back of card */
  .card-back {
    top: 100px;
    background: var(--teal);
    color: #fff;
    display: flex;
    flex-direction: column;
    align-items: center;
    justify-content: center;
    gap: 46px;
  }
  .card-back .org-name {
    font-family: "Michroma", sans-serif;
    font-weight: 400;
    font-size: 36px;
    letter-spacing: 3px;
    text-transform: uppercase;
    text-align: center;
    line-height: 1.35;
  }
  .card-back .tagline {
    font-size: 30px;
    color: #fff;
  }
  /* Front of card */
  .card-front {
    top: 640px;
    background: var(--paper);
    color: var(--ink);
  }
  .brand {
    position: absolute;
    left: 70px;
    top: 52px;
    display: flex;
    align-items: center;
    gap: 18px;
  }
  .brand-dot {
    width: 30px; height: 30px;
    border-radius: 50%;
    background: var(--teal);
  }
  .brand-name {
    font-family: "Michroma", sans-serif;
    font-size: 27px;
    letter-spacing: 2px;
    color: var(--teal);
    text-transform: uppercase;
  }
  .person {
    position: absolute;
    left: 0; right: 0;
    top: 140px;
    text-align: center;
  }
  .person-name {
    font-family: "Michroma", sans-serif;
    font-weight: 400;
    font-size: 24px;
    letter-spacing: 3px;
    color: var(--teal);
    text-transform: uppercase;
  }
  .person-title {
    margin-top: 10px;
    font-size: 19px;
  }
  .web-row {
    position: absolute;
    left: 60px; right: 60px;
    top: 238px;
    display: flex;
    align-items: center;
    gap: 16px;
    font-size: 18px;
  }
  .web-row .rule { flex: 1; height: 1px; background: var(--rule); }
  .contact {
    position: absolute;
    left: 60px; right: 60px;
    top: 290px;
    display: flex;
    justify-content: center;
    gap: 28px;
    font-size: 18px;
    line-height: 1.7;
  }
  .contact .divider { width: 1px; background: var(--rule); }
  .address { display: flex; gap: 12px; text-align: right; }
  .lines { display: flex; flex-direction: column; gap: 6px; }
  .line { display: flex; align-items: center; gap: 12px; }
  .icon { width: 24px; height: 24px; flex: none; }
</style>
</head>
<body>
  <section class="card card-back">
    <h1 class="org-name">Homeward Haven Center</h1>
    <p class="tagline">Guiding every family home</p>
  </section>

  <section class="card card-front">
    <div class="brand">
      <span class="brand-dot"></span>
      <span class="brand-name">Homeward Haven Center</span>
    </div>

    <div class="person">
      <h2 class="person-name">Daniel Marlowe</h2>
      <p class="person-title">Chairman</p>
    </div>

    <div class="web-row">
      <span class="rule"></span>
      <span class="website">www.homewardhaven.org</span>
      <span class="rule"></span>
    </div>

    <div class="contact">
      <div class="address">
        <div>P.O Box 50321<br>Dallas, Texas 75201</div>
        <svg class="icon" viewBox="0 0 24 24" aria-hidden="true">
          <circle cx="12" cy="12" r="12" fill="var(--teal)"/>
          <path d="M12 5a4.5 4.5 0 0 0-4.5 4.5c0 3.4 4.5 8.5 4.5 8.5s4.5-5.1 4.5-8.5A4.5 4.5 0 0 0 12 5z" fill="#fff"/>
          <circle cx="12" cy="9.5" r="1.7" fill="var(--teal)"/>
        </svg>
      </div>
      <span class="divider"></span>
      <div class="lines">
        <div class="line">
          <svg class="icon" viewBox="0 0 24 24" aria-hidden="true">
            <circle cx="12" cy="12" r="12" fill="var(--teal)"/>
            <path d="M8.5 6.5l2 2.2-1.2 1.5c.8 1.7 2 2.9 3.6 3.7l1.5-1.2 2.2 2-1.2 2c-4.3-.3-7.8-3.8-8.1-8.1z" fill="#fff"/>
          </svg>
          <span>214.555.0182</span>
        </div>
        <div class="line">
          <svg class="icon" viewBox="0 0 24 24" aria-hidden="true">
            <circle cx="12" cy="12" r="12" fill="var(--teal)"/>
            <rect x="6" y="8" width="12" height="8.5" rx="1" fill="#fff"/>
            <path d="M6.5 8.7l5.5 4 5.5-4" fill="none" stroke="var(--teal)" stroke-width="1.2"/>
          </svg>
          <span>daniel@homewardhaven.org</span>
        </div>
      </div>
    </div>
  </section>
</body>
</html>
```